Candle Rental Business seeks new website design

We need a new website design for a Candle hire business. The business rents out pillar candles for events such as weddings and corporate events. Our main target market is weddings. The business name is Hire a Lantern. The business name does not have a logo design.

We would like a website that is light in colours and creates a warm atmosphere. The design needs to be elegant and upmarket. There are different size candles that we hire out, ranging from 10cm diameter to 20cm diameter, flat, tall etc. All our candles are white in colour. Its just the size that differs.

We would also like to include a section for hiring out decor such as glassvases, candlebras, overlays and chairs sachets, chair covers. However, this is not the businesses main focus but an additional offering to customers.

Target Market(s)

Wedding venues and brides. Corporate events. School dances.

Industry/Entity Type

Hospitality

Logo Text

Hire a Lantern

Number of Pages Required

1 page

Font styles to use
Sans Serif
Script

Requirements
Must have
• Pictures of pillar candles. Plain white candles. The website must centre around candles.
Nice to have
• Different examples of candle centrepieces
Should not have
• Pictures must not be of brides. Pictures of surrounding is perferable.

```html
<!DOCTYPE html>
<html lang="en">
<head>
<meta charset="utf-8">
<title>Hire a Lantern – Candle Hire</title>
<link href="https://fonts.googleapis.com/css2?family=Questrial&family=Lato:ital,wght@0,400;0,700;1,400&display=swap" rel="stylesheet">
<style>
:root{
  --pink:#c9739f;
  --pink-light:#e58fbf;
  --purple:#9a70c4;
  --purple-dark:#7f59ad;
  --ink:#1d1d1d;
  --text:#333;
  --muted:#777;
  --footer:#2e2e2e;
  --footer-dark:#232323;
  --white:#fff;
}
*{box-sizing:border-box;margin:0;padding:0}
html,body{width:1200px;height:2651px;overflow:hidden;background:var(--white)}
body{position:relative;font-family:"Lato",sans-serif;color:var(--text)}
.abs{position:absolute}
.heading{font-family:"Questrial",sans-serif}

/* header + hero */
.hero{left:0;top:0;width:1200px;height:655px;background:radial-gradient(ellipse at 50% 30%,#f3d98a 0%,#b88b5c 18%,#6b4a3c 45%,#3b2a2a 100%)}
.hero-photo{position:absolute;inset:0;background:linear-gradient(180deg,rgba(60,30,30,.2),rgba(230,225,220,.35) 70%,rgba(200,195,190,.5))}
.topbar{left:0;top:0;width:1200px;height:100px;background:rgba(0,0,0,.45)}
.brand{left:132px;top:30px;display:flex;align-items:center;gap:14px;font-family:"Questrial",sans-serif;font-size:38px;color:var(--white)}
.brand-mark{width:36px;height:36px;background:var(--white);border-radius:4px}
.phone{right:66px;top:18px;display:flex;align-items:center;gap:10px;color:var(--pink-light);font-size:18px}
.phone-dot{width:26px;height:26px;border-radius:50%;background:var(--pink);display:flex;align-items:center;justify-content:center}
.nav{left:496px;top:58px;display:flex;font-size:14px;color:var(--white)}
.nav span{margin-right:40px}
.nav .active{position:relative}
.nav .active::after{content:"";position:absolute;left:0;right:0;bottom:-10px;height:3px;background:var(--white)}
.hero-caption{left:0;top:590px;width:1200px;height:65px;background:rgba(40,40,40,.55);color:var(--white);font-size:31px;padding:8px 0 0 131px;letter-spacing:.5px}

/* services */
.service{width:267px;height:134px;border-radius:6px;background:linear-gradient(180deg,#8a8a8a,#3a3a3a);box-shadow:0 10px 14px rgba(0,0,0,.2);color:var(--white);overflow:hidden}
.service svg{position:absolute;left:22px;top:18px}
.service .label{position:absolute;left:110px;top:18px;font-family:"Questrial",sans-serif;font-size:21px;line-height:24px}
.service .more{position:absolute;left:110px;top:78px;width:104px;height:30px;border:1px solid var(--white);font-size:13px;font-weight:700;text-align:center;line-height:28px}

/* welcome */
.welcome-title{left:131px;top:885px;font-size:28px;color:var(--ink);font-weight:400}
.welcome-title b{font-family:"Lato",sans-serif;font-weight:700}
.welcome-rule{left:131px;top:931px;width:533px;height:1px;background:#ccc}
.welcome-rule::before{content:"";position:absolute;left:0;top:-1px;width:110px;height:3px;background:var(--pink)}
.welcome-text{left:131px;top:946px;width:533px;font-size:13.5px;line-height:21px;color:#444}
.btn-pink{left:131px;top:1085px;width:113px;height:37px;background:var(--pink);color:var(--white);font-size:14px;font-weight:700;text-align:center;line-height:37px;border-radius:2px}
.video{left:739px;top:901px;width:330px;height:221px;border-radius:4px;overflow:hidden;background:linear-gradient(135deg,#6d6a6a,#2e2b2b 60%,#4a4545)}
.video-play{left:143px;top:80px;width:44px;height:44px;border-radius:50%;background:rgba(255,255,255,.85)}
.video-bar{left:0;bottom:0;width:330px;height:30px;background:#1a1a1a}

/* decor */
.decor{left:0;top:1179px;width:1200px;height:311px;background:radial-gradient(circle at 20% 30%,#b496d6 0,var(--purple) 40%,var(--purple-dark) 100%)}
.decor-title{left:0;top:1218px;width:1200px;text-align:center;font-size:28px;color:var(--white);font-weight:400}
.decor-title b{font-family:"Lato",sans-serif}
.decor-rule{left:420px;top:1266px;width:360px;height:1px;background:rgba(255,255,255,.6)}
.decor-item{top:1310px;width:180px;text-align:center;color:var(--white);font-size:18px;font-weight:700}
.decor-item .ring{width:78px;height:78px;margin:0 auto 20px;border:2px solid var(--white);border-radius:50%;display:flex;align-items:center;justify-content:center}
.decor-item .ring.on{background:var(--pink-light)}
.decor-sep{top:1310px;width:1px;height:110px;background:rgba(255,255,255,.3)}

/* testimonials */
.t-title{left:0;top:1544px;width:1200px;text-align:center;font-size:28px;color:var(--ink);font-weight:400}
.t-title b{font-family:"Lato",sans-serif}
.t-rule{left:420px;top:1594px;width:360px;height:1px;background:#ddd}
.t-rule::before{content:"";position:absolute;left:125px;top:-1px;width:110px;height:3px;background:var(--pink)}
.t-card{top:1623px;width:430px}
.t-avatar{position:absolute;left:0;top:0;width:96px;height:96px;border-radius:50%;border:4px solid var(--pink);background:linear-gradient(180deg,#c9b3a2,#7a8ba3)}
.t-name{position:absolute;left:117px;top:29px;font-size:14px;font-weight:700;color:#1f3c5c}
.t-role{position:absolute;left:117px;top:49px;font-size:12px;color:var(--purple)}
.t-quote{position:absolute;left:0;top:108px;width:430px;font-size:13px;line-height:26px;font-style:italic;color:#444;text-indent:24px}
.t-divider{left:599px;top:1630px;width:1px;height:205px;background:#ddd}
.dots{left:555px;top:1868px;display:flex;gap:11px}
.dots span{width:15px;height:15px;border-radius:50%;background:var(--ink)}
.dots span.off{background:var(--white);border:2px solid var(--ink)}

/* promo */
.promo{left:0;top:1949px;width:1200px;height:375px;background:radial-gradient(ellipse at 35% 60%,#d9cbb8 0%,#7a6d62 25%,#3a3534 60%,#2a2828 100%)}
.promo-text{left:511px;top:2015px;width:560px;color:var(--white)}
.promo-text h2{font-family:"Lato",sans-serif;font-size:25px;font-weight:700;letter-spacing:1px;line-height:32px}
.promo-text p{font-size:20px;line-height:29px}
.promo-text h3{font-size:18px;font-weight:700;line-height:26px;margin-top:10px}
.btn-outline{left:511px;top:2198px;width:148px;height:50px;border:1px solid var(--white);color:var(--white);font-size:17px;font-weight:700;text-align:center;line-height:48px}

/* footer */
.footer{left:0;top:2325px;width:1200px;height:326px;background:linear-gradient(180deg,var(--footer),var(--footer-dark))}
.f-head{top:2348px;font-size:16px;color:#ddd}
.f-rule{left:0;top:2386px;width:1200px;height:1px;background:#444}
.f-links{left:133px;top:2403px;font-size:12.5px;color:#ddd;line-height:30.5px;list-style:none}
.f-links li::before{content:"›";color:#888;margin-right:12px}
.news{left:306px;width:240px;font-size:12px;color:#ddd;line-height:16px}
.news .date{position:absolute;left:0;top:0;width:22px;height:30px;background:#555;color:#fff;font-size:10px;text-align:center;line-height:14px;font-weight:700}
.news .body{margin-left:32px}
.news b{color:var(--purple)}
.contact{left:601px;top:2403px;font-size:12.5px;color:#ddd;line-height:19px}
.contact-row{left:601px;font-size:12.5px;color:#ddd;display:flex;align-items:center;gap:12px}
.field{left:846px;width:221px;height:32px;background:#1f1f1f;border:1px solid #444;font-size:11px;color:#888;padding:8px 10px}
.submit{left:846px;width:100px;height:31px;background:var(--purple);color:#fff;font-weight:700;font-size:14px;text-align:center;line-height:31px}
.f-bottom{left:133px;top:2603px;width:934px;height:1px;background:#555}
.copy{left:133px;top:2616px;font-size:12.5px;color:#ddd}
.social{right:133px;top:2612px;display:flex;gap:6px}
.social span{width:24px;height:24px;background:#eee;border-radius:2px}
.social span:first-child{background:var(--purple)}
</style>
</head>
<body>

<div class="abs hero" role="img" aria-label="Wedding table centrepiece with a white pillar candle in cream roses and greenery, surrounded by wine glasses"><div class="hero-photo"></div></div>
<header>
  <div class="abs topbar"></div>
  <div class="abs brand"><span class="brand-mark"></span>Hire a Lantern</div>
  <div class="abs phone"><span class="phone-dot"><svg width="14" height="14" viewBox="0 0 24 24"><path fill="#fff" d="M6.6 10.8a15 15 0 006.6 6.6l2.2-2.2c.3-.3.7-.4 1-.2 1.1.4 2.3.6 3.6.6.6 0 1 .4 1 1V20c0 .6-.4 1-1 1A17 17 0 013 4c0-.6.4-1 1-1h3.5c.6 0 1 .4 1 1 0 1.3.2 2.5.6 3.6.1.3 0 .7-.2 1z"/></svg></span>(555)0142-736</div>
  <nav class="abs nav"><span class="active">Home</span><span>About Us</span><span>Our Products</span><span>Hire Candles</span><span>Décor Hire</span><span>Contact Us</span></nav>
</header>
<div class="abs hero-caption heading">Creating A Warm Atmosphere &amp; Special Touch To All Occasions</div>

<section>
  <div class="abs service" style="left:159px;top:693px">
    <svg width="70" height="96" viewBox="0 0 70 96"><path d="M35 8c6 12 10 18 6 26-3 5-9 5-12 0-4-8 0-14 6-26z" fill="#fff"/><rect x="14" y="44" width="42" height="48" rx="3" fill="none" stroke="#fff" stroke-width="4"/></svg>
    <div class="label">Hire<br>Candles</div><div class="more">Read More</div>
  </div>
  <div class="abs service" style="left:466px;top:693px">
    <svg width="70" height="96" viewBox="0 0 70 96"><path d="M35 10c5 10 8 15 5 21-2 4-8 4-10 0-3-6 0-11 5-21z" fill="#fff"/><ellipse cx="35" cy="52" rx="26" ry="8" fill="none" stroke="#fff" stroke-width="4"/><path d="M9 52v24c0 5 12 9 26 9s26-4 26-9V52" fill="none" stroke="#fff" stroke-width="4"/></svg>
    <div class="label">Personalised<br>Candles</div><div class="more">Read More</div>
  </div>
  <div class="abs service" style="left:772px;top:693px">
    <svg width="80" height="96" viewBox="0 0 80 96"><rect x="8" y="36" width="18" height="48" fill="#fff"/><rect x="31" y="22" width="18" height="62" fill="#fff"/><rect x="54" y="40" width="18" height="44" fill="#fff"/><circle cx="17" cy="28" r="3" fill="#fff"/><circle cx="40" cy="14" r="3" fill="#fff"/><circle cx="63" cy="32" r="3" fill="#fff"/></svg>
    <div class="label">Décor<br>Hire</div><div class="more">Read More</div>
  </div>
</section>

<section>
  <h1 class="abs welcome-title heading">Welcome to <b>HIRE A LANTERN</b></h1>
  <div class="abs welcome-rule"></div>
  <p class="abs welcome-text">Lorem ipsum dolor sit amet, consectetur adipiscing elit. Nulla in sollicitudin velit, bibendum velit. Cras vel facilisis ipsum, et venenatis risus. In egestas nunc etvb eros auctor sollicitu Etiam ut enim vitae magna volutpat venenatis vitae nonprof diam. Nam nunc velit, tristique a sapien euismod, pulvinar vestibulum dui. Morbi porttitor eu erat imperdiet pretium consequat fcilelis. Cras vel facilisis ipsum, et venenatis risus. In egestas nunc etvb eros auctor sollicitu.</p>
  <div class="abs btn-pink">READ MORE</div>
  <div class="abs video" role="img" aria-label="Video still of white pillar candles of different heights on a table in a living room">
    <div class="abs video-play"></div>
    <div class="abs video-bar">
      <svg width="330" height="30"><path d="M12 10l8 5-8 5z" fill="#fff"/><path d="M36 12h4l5-4v14l-5-4h-4z" fill="#fff"/><rect x="64" y="13" width="200" height="4" rx="2" fill="#555"/><rect x="64" y="13" width="80" height="4" rx="2" fill="#d22"/><path d="M305 9h8v2h-6v6h-2zM315 21h-8v-2h6v-6h2z" fill="#fff"/></svg>
    </div>
  </div>
</section>

<section>
  <div class="abs decor" role="img" aria-label="Soft purple background with blurred light bubbles"></div>
  <h2 class="abs decor-title heading">Our Decor <b>Hires</b></h2>
  <div class="abs decor-rule"></div>
  <div class="abs decor-item" style="left:161px"><div class="ring"><svg width="36" height="44" viewBox="0 0 36 44"><path d="M12 2h12l-2 10c6 6 6 24 0 30H14c-6-6-6-24 0-30z" fill="#fff"/></svg></div>Glass Vases</div>
  <div class="abs decor-sep" style="left:385px"></div>
  <div class="abs decor-item" style="left:407px"><div class="ring on"><svg width="44" height="44" viewBox="0 0 44 44"><path d="M6 18q16 12 32 0M22 10v28M14 40h16" stroke="#fff" stroke-width="3" fill="none"/><rect x="4" y="10" width="4" height="8" fill="#fff"/><rect x="20" y="4" width="4" height="8" fill="#fff"/><rect x="36" y="10" width="4" height="8" fill="#fff"/></svg></div>Candle Bars</div>
  <div class="abs decor-sep" style="left:609px"></div>
  <div class="abs decor-item" style="left:643px"><div class="ring"><svg width="32" height="44" viewBox="0 0 32 44"><path d="M8 22V8q8-8 16 0v14M5 22h22v6H5zM8 28v14M24 28v14" stroke="#fff" stroke-width="3" fill="none"/></svg></div>Chair Sachets</div>
  <div class="abs decor-sep" style="left:846px"></div>
  <div class="abs decor-item" style="left:852px"><div class="ring"><svg width="44" height="36" viewBox="0 0 44 36"><path d="M8 16V8q14-8 28 0v8M4 16h6v10h24V16h6v12H4zM8 28v4M36 28v4" stroke="#fff" stroke-width="3" fill="none"/></svg></div>Chair Covers</div>
</section>

<section>
  <h2 class="abs t-title heading">Client <b>Testimonials</b></h2>
  <div class="abs t-rule"></div>
  <div class="abs t-card" style="left:131px">
    <div class="t-avatar" role="img" aria-label="Client portrait"></div>
    <div class="t-name">Mr. Arlen Whitby</div><div class="t-role">Lorem Ipsum</div>
    <p class="t-quote">Utm tellus dolor, dapibus eget, elemen velmki cursus eleifelta arnean auctorbni wisi et urnam. Lorem ipsum dolor sit amet, conse ctetur adipiscing elit. Nulla in sollicitudin velit, bibendum velit.Cras vel facilisis ipsum, et venenatis risus.</p>
  </div>
  <div class="abs t-divider"></div>
  <div class="abs t-card" style="left:636px">
    <div class="t-avatar" role="img" aria-label="Client portrait"></div>
    <div class="t-name">Mr. Arlen Whitby</div><div class="t-role">Lorem Ipsum</div>
    <p class="t-quote">Utm tellus dolor, dapibus eget, elemen velmki cursus eleifelta arnean auctorbni wisi et urnam. Lorem ipsum dolor sit amet, conse ctetur adipiscing elit. Nulla in sollicitudin velit, bibendum velit.Cras vel facilisis ipsum, et venenatis risus.</p>
  </div>
  <div class="abs dots"><span></span><span class="off"></span><span></span><span></span></div>
</section>

<section>
  <div class="abs promo" role="img" aria-label="Lit white pillar candle on a silver beaded plate among festive decorations"></div>
  <div class="abs promo-text">
    <h2>We DESIGN, MANUFACTURE &amp; PERSONALISE</h2>
    <p>All Of Our CANDLES In Our Most Distinctive Handcrafted Manner!</p>
    <h3>Different Size Candles Ranging From<br>10cm Diameter To 20cm Diameter, Flat, Tall Etc</h3>
  </div>
  <div class="abs btn-outline">BUY NOW</div>
</section>

<footer>
  <div class="abs footer"></div>
  <div class="abs f-head heading" style="left:133px">Quick Links</div>
  <div class="abs f-head heading" style="left:306px">News / Updates</div>
  <div class="abs f-head heading" style="left:601px">Contact Detail</div>
  <div class="abs f-head heading" style="left:846px">Quick Contact</div>
  <div class="abs f-rule"></div>
  <ul class="abs f-links"><li>Home</li><li>About Us</li><li>Our Products</li><li>Hire Candles</li><li>Décor Hire</li><li>Contact Us</li></ul>
  <div class="abs news" style="top:2403px"><div class="date">22<br>MAR</div><div class="body"><b>Duis autem vel eumsodn</b><br>Lorem ipsum dolor sit ametn nk consectetuer adipiscing elit.</div></div>
  <div class="abs news" style="top:2466px"><div class="date">22<br>MAR</div><div class="body"><b>Duis autem vel eumsodn</b><br>Lorem ipsum dolor sit ametn nk consectetuer adipiscing elit.</div></div>
  <div class="abs news" style="top:2529px"><div class="date">22<br>MAR</div><div class="body"><b>Duis autem vel eumsodn</b><br>Lorem ipsum dolor sit ametn nk consectetuer adipiscing elit.</div></div>
  <div class="abs contact"><b>Hire a Lantern</b><br>16 Lorem ipsum dolor sit sed<br>benetion, Street no-123456</div>
  <div class="abs contact-row" style="top:2480px"><svg width="12" height="12" viewBox="0 0 24 24"><path fill="#bbb" d="M6.6 10.8a15 15 0 006.6 6.6l2.2-2.2c.3-.3.7-.4 1-.2 1.1.4 2.3.6 3.6.6.6 0 1 .4 1 1V20c0 .6-.4 1-1 1A17 17 0 013 4c0-.6.4-1 1-1h3.5c.6 0 1 .4 1 1 0 1.3.2 2.5.6 3.6.1.3 0 .7-.2 1z"/></svg>555-014-2781</div>
  <div class="abs contact-row" style="top:2520px"><svg width="12" height="12" viewBox="0 0 12 12"><rect x="3" y="0" width="6" height="4" fill="#bbb"/><rect x="0" y="4" width="12" height="5" fill="#bbb"/><rect x="3" y="8" width="6" height="4" fill="#bbb"/></svg>555-019-4462</div>
  <div class="abs contact-row" style="top:2564px"><svg width="12" height="10" viewBox="0 0 12 10"><rect x="0" y="0" width="12" height="10" fill="#bbb"/><path d="M0 0l6 5 6-5" stroke="#333" fill="none"/></svg>info@hirealantern.example</div>
  <div class="abs field" style="top:2403px">Name</div>
  <div class="abs field" style="top:2440px">Email</div>
  <div class="abs field" style="top:2477px;height:68px">Message</div>
  <div class="abs submit" style="top:2553px">SUBMIT</div>
  <div class="abs f-bottom"></div>
  <div class="abs copy">Copyright © 2016 HIRE A LANTERN | All Rights Reserved.</div>
  <div class="abs social"><span></span><span></span><span></span><span></span></div>
</footer>

</body>
</html>
```